Meadowlark Property Review is a leading provider of residential appraisal and home inspection products in S

I need a business card/logo designed that obviously describes my business. We are a residential appraisal and home inspection company in Springfield, MO. We offer residential appraisals, home inspection, pest inspection and radon gas measurement. We have been in business for 18 years and hold state certified residential appraisal licenses and OBREX certified home inspection licenses. I have a logo that I really like and will attach, but would be open to new suggestions. I like more modern designs than traditional and would like a two sided card with our services, licenses and qualifications on the back.

```html
<!DOCTYPE html>
<html lang="en">
<head>
<meta charset="utf-8">
<title>Meadowlark Property Review – Business Card</title>
<link href="https://fonts.googleapis.com/css2?family=PT+Sans:ital,wght@0,400;0,700;1,400&display=swap" rel="stylesheet">
<style>
  :root {
    --stage: #3b3b3b;
    --brown: #8f6a42;
    --brown-dark: #7a5834;
    --orange: #f0891e;
    --paper: #f6f6f6;
    --white: #ffffff;
    --ink-grey: #4a4a4a;
  }
  * { margin: 0; padding: 0; box-sizing: border-box; }
  html, body {
    width: 1200px; height: 750px; overflow: hidden;
    background: var(--stage);
    font-family: "PT Sans", sans-serif;
  }
  .stage { position: relative; width: 1200px; height: 750px; }
  .card {
    position: absolute; top: 228px;
    width: 461px; height: 262px; overflow: hidden;
  }
  /* front side */
  .card-front { left: 124px; background: var(--brown); }
  .holder { position: absolute; left: 16px; top: 14px; }
  .holder-name { color: var(--orange); font-size: 18px; font-weight: 700; line-height: 1.1; }
  .holder-role { color: var(--white); font-size: 13px; margin-top: 2px; }
  .contact {
    position: absolute; right: 21px; top: 18px;
    color: var(--white); font-size: 11px; text-align: right; line-height: 17px;
  }
  .contact-address { margin-bottom: 4px; }
  .contact-line { display: flex; justify-content: flex-end; align-items: center; gap: 9px; height: 17.5px; }
  .contact-line svg { width: 12px; height: 12px; fill: var(--orange); flex: none; }
  .brand-panel {
    position: absolute; left: 0; bottom: 0; width: 300px; height: 96px;
    background: var(--paper);
    border-top: 5px solid var(--orange);
    display: flex; align-items: center; justify-content: center; gap: 8px;
  }
  .brand-mark { width: 10px; height: 10px; background: var(--orange); }
  .brand-name { color: var(--brown-dark); font-size: 19px; font-weight: 700; }

  /* back side */
  .card-back { left: 618px; background: var(--paper); }
  .back-brand {
    position: absolute; left: 0; right: 0; top: 110px;
    text-align: center; color: var(--brown); font-size: 24px; font-weight: 700;
  }
  .services {
    position: absolute; left: 0; right: 0; top: 199px;
    text-align: center; color: var(--ink-grey); font-size: 12px; font-style: italic; line-height: 18px;
  }
  .services .dot { color: var(--orange); font-style: normal; }
</style>
</head>
<body>
<main class="stage">
  <section class="card card-front" aria-label="Card front">
    <div class="holder">
      <p class="holder-name">Dana Whitlow</p>
      <p class="holder-role">CEO/Founder</p>
    </div>
    <div class="contact">
      <p class="contact-address">4120 Cedar Hollow Road<br>Springfield, Missouri 65804</p>
      <p class="contact-line">417 555 0182
        <svg viewBox="0 0 24 24" aria-hidden="true"><path d="M6.6 10.8a15 15 0 0 0 6.6 6.6l2.2-2.2c.3-.3.7-.4 1-.2 1.1.4 2.3.6 3.6.6.6 0 1 .4 1 1V20c0 .6-.4 1-1 1A17 17 0 0 1 3 4c0-.6.4-1 1-1h3.5c.6 0 1 .4 1 1 0 1.3.2 2.5.6 3.6.1.3 0 .7-.2 1z"/></svg>
      </p>
      <p class="contact-line">417 555 0196
        <svg viewBox="0 0 24 24" aria-hidden="true"><path d="M6 3h12v5H6zM2 10h20v8h-4v3H6v-3H2zm6 5v4h8v-4z"/></svg>
      </p>
      <p class="contact-line">dana@meadowlarkreview.com
        <svg viewBox="0 0 24 24" aria-hidden="true"><path d="M2 5h20v14H2zm2 2v.5l8 5 8-5V7l-8 5z"/></svg>
      </p>
      <p class="contact-line">www.meadowlarkreview.com
        <svg viewBox="0 0 24 24" aria-hidden="true"><path d="M12 2a10 10 0 1 0 0 20 10 10 0 0 0 0-20zm-1 17.9A8 8 0 0 1 4.1 10L9 15v1c0 1.1.9 2 2 2zm6.9-2.5c-.3-.8-1-1.4-1.9-1.4h-1v-3c0-.6-.4-1-1-1H8v-2h2c.6 0 1-.4 1-1V7h2c1.1 0 2-.9 2-2v-.4a8 8 0 0 1 2.9 12.8z"/></svg>
      </p>
    </div>
    <div class="brand-panel">
      <span class="brand-mark" aria-hidden="true"></span>
      <span class="brand-name">Meadowlark Property Review</span>
    </div>
  </section>

  <section class="card card-back" aria-label="Card back">
    <p class="back-brand">Meadowlark Property Review</p>
    <p class="services">Residential appraisals <span class="dot">•</span> Home inspection<br>Pest inspection and radon gas measurement.</p>
  </section>
</main>
</body>
</html>
```